Fernhale Business Card Design

We are looking for a fresh business card design for our new logo. We would like a business card that is unique but friendly. We are in the window coverings business offering blinds, shutters and shades for homes.

Target Market(s)

Targeting the end-consumer

Industry/Entity Type

Business

Requirements
Must have
• Must have a dedicates space for a photo of our sales person. Must contain our new logo (attached).

```html
<!DOCTYPE html>
<html lang="en">
<head>
<meta charset="utf-8">
<title>Fernhale Business Card</title>
<link href="https://fonts.googleapis.com/css2?family=Oswald:wght@500&family=Work+Sans:wght@400;500&display=swap" rel="stylesheet">
<style>
  :root {
    --stage: #161616;
    --card-top: #2b2b2b;
    --card-bottom: #222222;
    --green: #7dc242;
    --white: #f2f2f2;
    --silver: #b9b9b9;
    --mark-line: #111111;
    --photo-light: #4a4a4a;
    --photo-dark: #343434;
  }
  * { margin: 0; padding: 0; box-sizing: border-box; }
  html, body {
    width: 1200px; height: 900px; overflow: hidden;
    background: var(--stage);
    font-family: "Work Sans", sans-serif;
  }
  .canvas { position: relative; width: 1200px; height: 900px; }
  .card {
    position: absolute; left: 250px; width: 700px; height: 400px;
    background: linear-gradient(160deg, var(--card-top), var(--card-bottom));
    box-shadow: 0 14px 30px rgba(0,0,0,.55);
    overflow: hidden;
  }
  .card::after {
    content: ""; position: absolute; left: 0; right: 0; bottom: 0;
    height: 7px; background: var(--green);
  }
  .card--front { top: 35px; }
  .card--back { top: 465px; }

  /* front */
  .brand {
    position: absolute; left: 0; right: 0; top: 120px;
    display: flex; align-items: center; justify-content: center; gap: 26px;
  }
  .brand__square {
    width: 88px; height: 88px;
    border: 3px solid var(--mark-line);
    border-radius: 6px;
  }
  .brand__name {
    font-size: 76px; font-weight: 500; color: var(--silver);
    letter-spacing: 1px; line-height: 1;
  }
  .front-web {
    position: absolute; left: 0; right: 0; bottom: 42px;
    text-align: center; color: var(--white);
    font-size: 16px; letter-spacing: 1.5px;
  }

  /* back */
  .portrait {
    position: absolute; left: 40px; top: 100px;
    width: 120px; height: 150px;
    background: linear-gradient(180deg, var(--photo-light), var(--photo-dark));
    border-bottom: 4px solid var(--green);
  }
  .identity {
    position: absolute; left: 185px; top: 148px;
  }
  .identity__name {
    font-family: "Oswald", sans-serif; font-weight: 500;
    font-size: 40px; color: var(--green); line-height: 1;
    letter-spacing: 1px; text-transform: uppercase;
    white-space: nowrap;
  }
  .identity__role {
    margin-top: 10px; font-size: 15px; color: var(--white);
    letter-spacing: 2px; text-transform: uppercase;
  }
  .divider {
    position: absolute; left: 398px; top: 140px;
    width: 3px; height: 84px; background: var(--green);
  }
  .contacts {
    position: absolute; left: 418px; top: 142px; list-style: none;
  }
  .contacts li {
    display: flex; align-items: center; gap: 10px;
    font-size: 15px; color: var(--white); letter-spacing: .4px;
    height: 27px; white-space: nowrap;
  }
  .contacts svg { width: 14px; height: 14px; flex: none; }
  .accent { color: var(--green); }
  .address {
    position: absolute; left: 120px; bottom: 52px;
    display: flex; align-items: center; gap: 14px;
    color: var(--white); font-size: 18px; letter-spacing: 1px;
  }
  .address__square {
    width: 22px; height: 22px; border: 2px solid var(--silver); border-radius: 3px;
  }
</style>
</head>
<body>
<main class="canvas">

  <section class="card card--front" aria-label="Card front">
    <div class="brand">
      <span class="brand__square"></span>
      <span class="brand__name">Fernhale</span>
    </div>
    <p class="front-web">www.fernhaleliving.com</p>
  </section>

  <section class="card card--back" aria-label="Card back">
    <div class="portrait" role="img" aria-label="Photo of the sales person"></div>
    <div class="identity">
      <h1 class="identity__name">Daniel Orr</h1>
      <p class="identity__role">Sales Manager</p>
    </div>
    <span class="divider"></span>
    <ul class="contacts">
      <li>
        <svg viewBox="0 0 16 16" aria-hidden="true"><path fill="#7dc242" d="M3.5 1.5 6 1l1.3 3.2-1.6 1.2a8 8 0 0 0 4.9 4.9l1.2-1.6L15 10l-.5 2.5c-.2.9-1 1.5-1.9 1.4C6.9 13.4 2.6 9.1 2.1 3.4 2 2.5 2.6 1.7 3.5 1.5z"/></svg>
        +44 (0)1632 960418
      </li>
      <li>
        <svg viewBox="0 0 16 16" aria-hidden="true"><rect x="1" y="3" width="14" height="10" fill="#7dc242"/><path d="M1 3.5 8 9l7-5.5" fill="none" stroke="#242424" stroke-width="1.4"/></svg>
        dorr@fernhaleblinds.com
      </li>
      <li>
        <svg viewBox="0 0 16 16" aria-hidden="true"><g fill="none" stroke="#7dc242" stroke-width="1.4"><circle cx="8" cy="8" r="6.5"/><ellipse cx="8" cy="8" rx="3" ry="6.5"/><path d="M1.5 8h13M2.5 4.8h11M2.5 11.2h11"/></g></svg>
        <span>www.<span class="accent">fernhaleblinds</span>.com</span>
      </li>
    </ul>
    <p class="address">
      <span class="address__square"></span>
      18 Mill Lane Kilbride, Scotland KB4 2TR
    </p>
  </section>

</main>
</body>
</html>
```